New business card/stationary for a consulting company

I am looking for a clean and very professional looking business card for my consulting company as well as corresponding stationary. I am uploading our logo. I like simple and powerful for the feel. No graphics but I am open on everything else. Below is my contact information but would like the final to be in a version I can add my employees information into and print. Thank you.

Daniel Whitcombe
dan@ferncliffadvisory.com
2870 North 9th Avenue, Summit Floor, Elm Ridge, Illinois 60531
www.ferncliffadvisory.com

Industry/Entity Type

Consulting

Contact Information for Business Card

Daniel Whitcombe
dan@ferncliffadvisory.com
www.ferncliffadvisory.com

Font styles to use
Serif
Sans Serif

Requirements
Must have
• Our logo and the business card details.
Nice to have
• our website www.ferncliffadvisory.com

```html
<!DOCTYPE html>
<html lang="en">
<head>
<meta charset="utf-8">
<title>Ferncliff Advisory – Business Card</title>
<link rel="stylesheet" href="https://fonts.googleapis.com/css2?family=Cinzel:wght@700&family=Roboto:wght@400;500&family=Tenor+Sans&display=swap">
<style>
  :root {
    --navy: #03046a;
    --paper: #f4f4f4;
    --white: #ffffff;
    --backdrop: #e9e6e2;
  }
  * { margin: 0; padding: 0; box-sizing: border-box; }
  html, body { width: 1200px; height: 960px; overflow: hidden; }
  body { background: var(--backdrop); position: relative; font-family: "Roboto", sans-serif; }

  .card {
    position: absolute;
    width: 600px;
    height: 343px;
    box-shadow: 0 3px 8px rgba(0,0,0,0.25);
    overflow: hidden;
  }
  .card--front { left: 302px; top: 129px; background: var(--paper); }
  .card--back { left: 299px; top: 488px; background: var(--navy); }

  /* Front: brand zone */
  .brand {
    position: absolute;
    left: 0; right: 0;
    display: flex;
    align-items: center;
    justify-content: center;
    gap: 14px;
    font-family: "Tenor Sans", sans-serif;
    letter-spacing: 1px;
  }
  .card--front .brand { top: 112px; color: var(--navy); font-size: 25px; }
  .brand__square { width: 22px; height: 22px; background: currentColor; flex: none; }

  /* Front: divider and contact band */
  .divider {
    position: absolute; left: 0; right: 0; top: 193px;
    height: 2px; background: var(--navy);
  }
  .contact-band {
    position: absolute; left: 0; right: 0; top: 199px; bottom: 0;
    background: var(--navy); color: var(--white);
  }
  .person {
    position: absolute; right: 338px; top: 42px; text-align: right;
  }
  .person__name {
    font-family: "Cinzel", serif; font-weight: 700;
    font-size: 19px; letter-spacing: 0.5px; line-height: 1.2;
  }
  .person__email { font-size: 14px; line-height: 1.3; }
  .address {
    position: absolute; left: 290px; top: 40px;
    font-size: 14px; line-height: 18px;
  }
  .address__web { font-weight: 500; }

  /* Back */
  .card--back .brand { top: 150px; color: var(--white); font-size: 30px; }
  .card--back .brand__square { width: 26px; height: 26px; }
  .back__web {
    position: absolute; left: 0; right: 0; top: 287px;
    text-align: center; color: var(--white);
    font-family: "Tenor Sans", sans-serif;
    font-size: 12.5px; letter-spacing: 3px;
  }
</style>
</head>
<body>
  <section class="card card--front" aria-label="Business card front">
    <div class="brand">
      <span class="brand__square"></span>
      <span class="brand__name">FERNCLIFF ADVISORY</span>
    </div>
    <div class="divider"></div>
    <div class="contact-band">
      <div class="person">
        <div class="person__name">Daniel Whitcombe</div>
        <div class="person__email">dan@ferncliffadvisory.com</div>
      </div>
      <div class="address">
        <div>2870 North 9th Avenue</div>
        <div>Summit Floor, Elm Ridge, Illinois 60531</div>
        <div class="address__web">FERNCLIFFADVISORY.COM</div>
      </div>
    </div>
  </section>

  <section class="card card--back" aria-label="Business card back">
    <div class="brand">
      <span class="brand__square"></span>
      <span class="brand__name">FERNCLIFF ADVISORY</span>
    </div>
    <div class="back__web">WWW.FERNCLIFFADVISORY.COM</div>
  </section>
</body>
</html>
```